Business card for Sports Apparel business

DOUBLE SIDED DESIGN
We need business cards for a new sports apparel business. We are developing a protective headband for soccer initially.
Torvalle is focused on designing and developing head protection products to reduce the likelihood of concussion when playing sports. Exploring and understanding medical insights, material science research, current and former players experiences and governing bodies guidelines has allowed Torvalle to develop the safety, style, form and function requirements of a suitable product to bring to market.
Target Market(s)
Mums buying kits for the sons and daughters. Amateur footballers.
Industry/Entity Type
Sporting Good
Contact Information for Business Card
Martin Ashworth - CEO
Mobile: +44 7431589027
Email: martin@torvalle.co.uk
Tel: 0208 5519372
Helena Pargeter - COO
Mob: +44 7385 640117
Email: helena@torvalle.co.uk
Tel: 0208 5519372
Duncan Farrow - CCO
Mob: +44 7564 293081
Email: duncan@torvalle.co.uk
Tel: 0208 5519372
Look and feel
Each slider illustrates characteristics of the customer's brand and the style your logo design should communicate.

```html
<!DOCTYPE html>
<html lang="en">
<head>
<meta charset="utf-8">
<title>Torvalle Business Card</title>
<link rel="stylesheet" href="https://fonts.googleapis.com/css2?family=Montserrat:wght@400;500;600&family=Oswald:wght@500&display=swap">
<style>
  :root {
    --bg: #3a3631;
    --card: #ffffff;
    --blue: #0f5c9c;
    --grey: #5b5b5b;
    --ink: #333333;
  }
  * { box-sizing: border-box; margin: 0; padding: 0; }
  html, body { width: 1200px; height: 930px; overflow: hidden; }
  body {
    background: var(--bg);
    position: relative;
    font-family: "Montserrat", sans-serif;
  }
  .card {
    position: absolute;
    width: 560px;
    height: 320px;
    background: var(--card);
    border-radius: 22px;
    border-bottom: 7px solid var(--blue);
    box-shadow: 0 12px 26px rgba(0,0,0,0.35);
    overflow: hidden;
  }
  .card--front { left: 80px; top: 90px; }
  .card--back { left: 560px; top: 500px; }

  .wordmark {
    position: absolute;
    display: flex;
    align-items: center;
    gap: 14px;
    font-weight: 600;
    color: var(--grey);
    letter-spacing: 0.02em;
  }
  .wordmark__square {
    width: 26px;
    height: 26px;
    background: var(--blue);
  }
  .card--front .wordmark { left: 0; right: 0; top: 115px; justify-content: center; font-size: 56px; }
  .card--back .wordmark { left: 0; right: 0; top: 60px; justify-content: center; font-size: 60px; }
  .card--back .wordmark__square { width: 30px; height: 30px; }

  .site {
    position: absolute;
    left: 0; right: 0; bottom: 34px;
    text-align: center;
    font-size: 14px;
    font-weight: 500;
    letter-spacing: 0.12em;
    color: var(--ink);
  }
  .site strong, .contact strong { color: var(--blue); font-weight: 600; }

  .person {
    position: absolute;
    left: 70px;
    top: 205px;
    text-align: right;
  }
  .person__name {
    font-family: "Oswald", sans-serif;
    font-weight: 500;
    font-size: 27px;
    letter-spacing: 0.03em;
    color: var(--blue);
    text-transform: uppercase;
    line-height: 1;
  }
  .person__role {
    font-size: 17px;
    letter-spacing: 0.12em;
    color: var(--grey);
    margin-top: 4px;
  }
  .divider {
    position: absolute;
    left: 315px;
    top: 180px;
    width: 2px;
    height: 92px;
    background: var(--blue);
  }
  .contacts {
    position: absolute;
    left: 338px;
    top: 180px;
    list-style: none;
  }
  .contact {
    display: flex;
    align-items: center;
    gap: 9px;
    font-size: 16px;
    color: var(--ink);
    line-height: 23px;
  }
  .contact svg { width: 13px; height: 13px; flex: none; }
</style>
</head>
<body>
  <section class="card card--front" aria-label="Card front">
    <div class="wordmark"><span class="wordmark__square"></span>TORVALLE</div>
    <p class="site">www.<strong>torvalle</strong>.co.uk</p>
  </section>

  <section class="card card--back" aria-label="Card back">
    <div class="wordmark"><span class="wordmark__square"></span>TORVALLE</div>
    <div class="person">
      <p class="person__name">Helena Pargeter</p>
      <p class="person__role">COO</p>
    </div>
    <div class="divider"></div>
    <ul class="contacts">
      <li class="contact">
        <svg viewBox="0 0 16 16" aria-hidden="true"><path fill="#0f5c9c" d="M3 1l3 3-1.5 2a9 9 0 0 0 5.5 5.5L12 10l3 3-2 2C7 15 1 9 1 3z"/></svg>
        0208 5519372
      </li>
      <li class="contact">
        <svg viewBox="0 0 16 16" aria-hidden="true"><rect x="4" y="1" width="8" height="14" rx="1.5" fill="none" stroke="#0f5c9c" stroke-width="1.8"/><circle cx="8" cy="12.3" r="1" fill="#0f5c9c"/></svg>
        +44 7385 640117
      </li>
      <li class="contact">
        <svg viewBox="0 0 16 16" aria-hidden="true"><rect x="1.5" y="3.5" width="13" height="9" fill="none" stroke="#0f5c9c" stroke-width="1.6"/><path d="M1.5 3.5L8 9l6.5-5.5" fill="none" stroke="#0f5c9c" stroke-width="1.6"/></svg>
        helena@torvalle.co.uk
      </li>
      <li class="contact">
        <svg viewBox="0 0 16 16" aria-hidden="true"><circle cx="8" cy="8" r="6.5" fill="none" stroke="#0f5c9c" stroke-width="1.5"/><ellipse cx="8" cy="8" rx="2.8" ry="6.5" fill="none" stroke="#0f5c9c" stroke-width="1.2"/><path d="M1.5 8h13" stroke="#0f5c9c" stroke-width="1.2"/></svg>
        www.<strong>torvalle</strong>.co.uk
      </li>
    </ul>
  </section>
</body>
</html>
```